Wealth Education Business Needs Sharp Business Card Design

We need a business card design for a recently launched investor education business called Harbor Crest.

The final design should promote security, empowerment, self improvement and financial gain. The card will ideally promote the stature of the business.

For more information and colours please visit harborcrest.com.au

Target Market(s)

Corporate executives and high net worth individuals

Industry/Entity Type

Education

Contact Information for Business Card

```html
<!DOCTYPE html>
<html lang="en">
<head>
<meta charset="utf-8">
<title>Harbor Crest – Business Card</title>
<link href="https://fonts.googleapis.com/css2?family=Lato:wght@400;700&display=swap" rel="stylesheet">
<style>
  :root {
    --bg: #e9e9e9;
    --card: #ffffff;
    --ink: #2b2b2b;
    --logo-ink: #3a3a3c;
    --teal: #1d7f86;
    --rule: #4f8fc9;
    --icon: #23606b;
  }
  * { margin: 0; padding: 0; box-sizing: border-box; }
  html, body { width: 1200px; height: 720px; overflow: hidden; }
  body {
    background: var(--bg);
    font-family: "Lato", sans-serif;
    color: var(--ink);
    position: relative;
  }
  .card {
    position: absolute;
    top: 241px;
    width: 420px;
    height: 240px;
    background: var(--card);
    border-radius: 14px;
    box-shadow: 0 0 0 1px rgba(0,0,0,0.04);
  }
  .card--front { left: 148px; }
  .card--back { left: 633px; }

  .wordmark {
    display: flex;
    align-items: center;
    gap: 12px;
    color: var(--logo-ink);
    font-weight: 400;
    text-transform: uppercase;
    white-space: nowrap;
  }
  .wordmark__dot {
    border-radius: 50%;
    background: var(--teal);
    flex: none;
  }
  .card--front .wordmark {
    position: absolute;
    top: 30px;
    left: 0; right: 0;
    justify-content: center;
    font-size: 33px;
    letter-spacing: 6px;
  }
  .card--front .wordmark__dot { width: 30px; height: 30px; }

  .card--back .wordmark {
    position: absolute;
    right: 22px;
    top: 194px;
    font-size: 17px;
    letter-spacing: 3px;
    gap: 7px;
  }
  .card--back .wordmark__dot { width: 15px; height: 15px; }

  .person {
    position: absolute;
    top: 117px;
    left: 0; right: 0;
    text-align: center;
  }
  .person__name {
    font-size: 16px;
    font-weight: 700;
    color: var(--teal);
    line-height: 20px;
  }
  .person__role {
    display: flex;
    align-items: center;
    justify-content: center;
    gap: 8px;
    font-size: 11px;
    font-weight: 700;
    line-height: 14px;
    margin-top: 1px;
  }
  .person__rule {
    width: 112px;
    height: 1.5px;
  }
  .person__rule--left { background: linear-gradient(to right, rgba(79,143,201,0), var(--rule)); }
  .person__rule--right { background: linear-gradient(to left, rgba(79,143,201,0), var(--rule)); }

  .contacts {
    position: absolute;
    left: 16px;
    top: 167px;
    list-style: none;
    font-size: 12.5px;
    line-height: 15.6px;
  }
  .contacts li { display: flex; align-items: center; gap: 5px; }
  .contacts svg { width: 11px; height: 11px; fill: var(--icon); flex: none; }

  .address {
    position: absolute;
    right: 17px;
    top: 186px;
    font-size: 12.5px;
    line-height: 15px;
    text-align: right;
    font-style: normal;
  }
  .address__line { display: flex; align-items: center; justify-content: flex-end; gap: 4px; }
  .address__line--indent { padding-right: 16px; }
  .address svg { width: 12px; height: 12px; fill: var(--teal); }
</style>
</head>
<body>

<section class="card card--front" aria-label="Business card front">
  <div class="wordmark"><span class="wordmark__dot"></span>Harbor Crest</div>

  <div class="person">
    <div class="person__name">Marcus Hale</div>
    <div class="person__role">
      <span class="person__rule person__rule--left"></span>
      Director
      <span class="person__rule person__rule--right"></span>
    </div>
  </div>

  <ul class="contacts">
    <li>
      <svg viewBox="0 0 24 24"><path d="M3 8c0-3 4-4 9-4s9 1 9 4v2h-5V8H8v2H3zM6 11h12l3 9H3z"/></svg>
      1300 418 275
    </li>
    <li>
      <svg viewBox="0 0 24 24"><path d="M7 1h10a2 2 0 0 1 2 2v18a2 2 0 0 1-2 2H7a2 2 0 0 1-2-2V3a2 2 0 0 1 2-2zm0 3v14h10V4zm5 15.5a1.2 1.2 0 1 0 0 2.4 1.2 1.2 0 0 0 0-2.4z"/></svg>
      +613 9472 5108
    </li>
    <li>
      <svg viewBox="0 0 24 24"><path d="M2 5h20v14H2zm2 2v.5l8 5.5 8-5.5V7z"/></svg>
      support@harborcrest.com.au
    </li>
    <li>
      <svg viewBox="0 0 24 24"><path d="M12 1a11 11 0 1 0 0 22 11 11 0 0 0 0-22zm0 2c1.3 1.4 2.3 3.5 2.7 6H9.3C9.7 6.5 10.7 4.4 12 3zM3.3 11h4c0 .7-.1 1.3-.1 2s0 1.3.1 2h-4a9 9 0 0 1 0-4zm5.9 0h5.6a17 17 0 0 1 0 2H9.2a17 17 0 0 1 0-2zm7.5 0h4a9 9 0 0 1 0 4h-4c.1-.7.1-1.3.1-2s0-1.3-.1-2zM9.3 15h5.4c-.4 2.5-1.4 4.6-2.7 6-1.3-1.4-2.3-3.5-2.7-6z"/></svg>
      www.harborcrest.com.au
    </li>
  </ul>

  <address class="address">
    <span class="address__line">Level 2, 74 Harbour Street
      <svg viewBox="0 0 24 24"><path d="M12 2 1 12h3v9h6v-6h4v6h6v-9h3z"/></svg>
    </span>
    <span class="address__line address__line--indent">Docklands VIC 3008</span>
  </address>
</section>

<section class="card card--back" aria-label="Business card back">
  <div class="wordmark"><span class="wordmark__dot"></span>Harbor Crest</div>
</section>

</body>
</html>
```